Lantern Petals Website v.1 - attract floral shop franchisees

I need a simple information website for my new business. We are a franchisor of flower shops. The overall purpose of the website is to promote the company and the service, especially to potential franchisees and retailers. Only about 4 pages are required including homepage, About, For Supermarkets, For Franchisees, and Contact. No special functions are required except the site will have two separate inquiry forms that must be filled out online and submitted via automated email. Similarly, an email form should be linked from the Contact page. I have a logo and business cards designed by ArtMingle, and I would like the site to have a consistent color scheme and style. The key to design will be to express the joy and love associated with flowers and floral bouquets.
IMPORTANT - I will be exporting the website design to Wordpress CMS in a site hosted by HostNimbus. For smooth integration into WordPress hosted by HostNimbus, the designer should build the site using a WordPress-friendly format. Ideally, they should use HTML, CSS, and PHP. Creating a custom theme or using a page builder that exports to WordPress-compatible files is best. This ensures the site can be easily imported and managed within WordPress.

Target Market(s)

Potential franchisees (existing florists or creative types who might like to own a floral business) and supermarkets who might want us to run their floral department

Industry/Entity Type

Floral retailing

Requirements
Must have
• A brand theme that is beautiful, consistent throughout and builds on the logo design
Nice to have
• Show gender and ethnic diversity in customers and florists. Pictures of happy florists (for franchisees) and pictures of amazing floral department displays (for supermarkets)

```html
<!DOCTYPE html>
<html lang="en">
<head>
<meta charset="utf-8">
<title>Lantern Petals</title>
<link href="https://fonts.googleapis.com/css2?family=Oswald:wght@500&family=Questrial&family=Great+Vibes&display=swap" rel="stylesheet">
<style>
:root{
  --orange:#f0a500;
  --green:#0a8a3c;
  --cream:#fcf4e4;
  --ink:#1f1f1f;
  --text:#444;
  --white:#fff;
  --black:#000;
}
*{margin:0;padding:0;box-sizing:border-box}
html,body{width:1200px;height:3122px;overflow:hidden}
body{position:relative;background:var(--white);font-family:"Questrial",sans-serif;color:var(--text)}
.abs{position:absolute}
.script{font-family:"Great Vibes",cursive;color:var(--ink)}
.script em{font-style:normal;color:var(--orange)}

/* header */
.brand{left:142px;top:24px;display:flex;align-items:center;gap:12px}
.brand-dot{width:44px;height:44px;border-radius:50%;background:var(--orange)}
.brand-name{font-size:30px;color:var(--orange)}
.contact-bar{top:12px;right:141px;display:flex;gap:26px;font-size:14px;color:var(--ink)}
.contact-bar span{display:flex;align-items:center;gap:12px}
.cbadge{width:30px;height:30px;border-radius:50%;background:var(--cream);display:flex;align-items:center;justify-content:center}
.header-rule{left:442px;top:56px;width:617px;height:1px;background:#ddd}
.nav{top:75px;left:505px;display:flex;gap:50px;font-size:13px;color:var(--ink)}
.nav .active{color:var(--orange)}

/* hero */
.hero{left:0;top:109px;width:1200px;height:529px;background:linear-gradient(90deg,#4a3a2c 0%,#7a6655 40%,#d8d3cc 70%,#b9b0a4 100%)}
.hero h1{position:absolute;left:142px;top:135px;font-family:"Oswald",sans-serif;font-weight:500;font-size:54px;line-height:67px;color:var(--white)}
.btn{position:absolute;left:142px;top:344px;width:126px;height:40px;background:var(--orange);color:var(--ink);font-size:14px;display:flex;align-items:center;justify-content:center;border-radius:2px}

/* about */
.about-photo{left:146px;top:710px;width:440px;height:440px;border-radius:50%;background:linear-gradient(135deg,#6b4a33,#b48c6a 50%,#4d5a3a);border:9px solid var(--white);box-shadow:0 0 12px rgba(0,0,0,.18)}
.about-head{left:636px;top:705px;font-size:56px}
.divider{display:flex;align-items:center;gap:8px}
.divider i{display:block;width:42px;height:2px;background:var(--green)}
.divider b{display:block;width:14px;height:14px;border-radius:50%;background:var(--green)}
.about-div{left:636px;top:776px}
.about-text{left:636px;top:818px;width:406px;font-size:12.4px;line-height:23px}
.about-text p+p{margin-top:8px}
.about-wide{left:152px;top:1185px;width:896px;text-align:center;font-size:12.4px;line-height:23px}
.about-wide p+p{margin-top:7px}

/* partner */
.partner{left:0;top:1410px;width:1200px;height:338px;background:linear-gradient(180deg,#2a2620,#3b2d2d 50%,#2c2a22)}
.partner-logo{position:absolute;left:0;width:1200px;top:110px;display:flex;justify-content:center;align-items:center;gap:10px;color:var(--white);font-size:16px;letter-spacing:4px}
.partner-logo span.ring{width:22px;height:22px;border-radius:50%;background:#9a9a9a}
.partner p{position:absolute;left:160px;width:880px;top:190px;text-align:center;color:var(--white);font-size:12.4px;line-height:23px}

/* gallery */
.gallery{left:142px;top:1831px;display:flex;gap:25px}
.tile{width:211px;height:270px;border-radius:10px;border:3px solid var(--white);box-shadow:0 0 8px rgba(0,0,0,.2)}
.t1{background:linear-gradient(160deg,#d9d2c7,#a63a4a 60%,#4f6b3a)}
.t2{background:linear-gradient(160deg,#c9b8a8,#6e7f9a 45%,#c73a3a)}
.t3{background:linear-gradient(180deg,#4a5a48,#a08a72 50%,#d9b8b8)}
.t4{background:linear-gradient(160deg,#e6e2da,#b63a3a 60%,#e9e2d6)}

/* testimonials */
.testi-head{left:0;width:1200px;top:2180px;text-align:center;font-size:56px}
.testi-div{left:538px;top:2247px}
.card{top:2328px;width:288px;height:352px;background:var(--cream);border-radius:12px;text-align:center}
.card .avatar{position:absolute;left:108px;top:-36px;width:72px;height:72px;border-radius:50%;border:4px solid var(--white);background:#c7a992}
.card p{position:absolute;left:30px;width:228px;top:84px;font-size:12.4px;line-height:23px;color:var(--ink)}
.card .who{position:absolute;left:0;width:288px;top:278px;font-size:24px}
.card .stars{position:absolute;left:0;width:288px;top:310px;color:var(--orange);font-size:15px;letter-spacing:2px}
.arrow{width:34px;height:34px;border-radius:50%;top:2488px;display:flex;align-items:center;justify-content:center}
.arrow.prev{left:92px;border:2px solid var(--green)}
.arrow.next{left:1074px;background:var(--green)}

/* footer */
.footer{left:0;top:2769px;width:1200px;height:353px;background:var(--black);color:var(--white)}
.fhead{position:absolute;top:58px;font-size:24px;color:var(--white)}
.fdiv{position:absolute;top:92px;display:flex;align-items:center;gap:5px}
.fdiv i{display:block;width:20px;height:1px;background:var(--white)}
.fdiv b{display:block;width:8px;height:8px;border-radius:50%;background:var(--white)}
.links{position:absolute;left:142px;top:104px;font-size:12.4px;line-height:33px}
.fcontact{position:absolute;left:412px;top:118px;font-size:12.4px;line-height:17px}
.fcontact li{list-style:none;display:flex;align-items:center;gap:12px;height:36px;margin-bottom:15px}
.fcontact .ic{width:36px;height:36px;border-radius:50%;background:var(--orange);display:flex;align-items:center;justify-content:center;flex:none}
.flogo{position:absolute;left:790px;top:110px;display:flex;align-items:center;gap:14px}
.flogo .brand-dot{width:60px;height:60px}
.flogo .brand-name{font-size:40px}
.social{position:absolute;left:852px;top:216px;display:flex;gap:6px}
.social i{display:block;width:29px;height:29px;border-radius:50%;border:2px solid var(--white)}
.frule{position:absolute;left:142px;top:307px;width:917px;height:1px;background:#333}
.copy{position:absolute;left:0;width:1200px;top:322px;text-align:center;font-size:12.4px}
</style>
</head>
<body>

<header>
  <div class="abs brand"><span class="brand-dot"></span><span class="brand-name">Lantern Petals</span></div>
  <div class="abs contact-bar">
    <span><span class="cbadge"><svg width="14" height="14" viewBox="0 0 24 24"><path fill="#0a8a3c" d="M6.6 10.8a15 15 0 0 0 6.6 6.6l2.2-2.2a1 1 0 0 1 1-.25 11.4 11.4 0 0 0 3.6.57 1 1 0 0 1 1 1V20a1 1 0 0 1-1 1A17 17 0 0 1 3 4a1 1 0 0 1 1-1h3.5a1 1 0 0 1 1 1c0 1.25.2 2.45.57 3.57a1 1 0 0 1-.25 1z"/></svg></span>123-456-7890</span>
    <span><span class="cbadge"><svg width="14" height="12" viewBox="0 0 24 18"><rect width="24" height="18" rx="2" fill="#0a8a3c"/><path d="M2 2l10 8 10-8" stroke="#fff" stroke-width="2" fill="none"/></svg></span>info@lanternpetals.com</span>
  </div>
  <div class="abs header-rule"></div>
  <nav class="abs nav"><span class="active">Home</span><span>About Us</span><span>For Supermarkets</span><span>For Franchisees</span></nav>
</header>

<section class="abs hero" role="img" aria-label="Smiling florist arranging white and red roses in a flower shop">
  <h1>Freshest Flowers<br>Artisan Designs<br>Franchise Opportunities</h1>
  <span class="btn">Contact Us</span>
</section>

<section>
  <div class="abs about-photo" role="img" aria-label="Founder arranging a bouquet in a floral studio"></div>
  <h2 class="abs script about-head">About <em>Us</em></h2>
  <div class="abs divider about-div"><i></i><b></b><i></i></div>
  <div class="abs about-text">
    <p>Fresh flowers convey beauty and love, and in our view should become something every person regularly enjoys.&nbsp; Lantern Petals is an entrepreneurial company created to make top quality fresh flowers and professionally-designed bouquets accessible to every consumer at affordable prices.</p>
    <p>Professional florists typically sell the finest quality stems, design the most beautiful bouquets and provide the finest customer service, but their costs – of floral products, retail spaces, labor and marketing – force them to pass high prices along to customers. Supermarket flower departments benefit from high customer footfall, economies of scale and low pricing, but their quality of stems and bouquets is typically poor, staffing is limited, and staff turnover is high which can result in inefficiency, wastage, poorly merchandised selections and limited service.</p>
  </div>
  <div class="abs about-wide">
    <p>Lantern Petals brings the best of professional florists and supermarkets together for the benefit of consumers.&nbsp; It supports a national network of owner-operator franchisees, who in many cases are multi-site professional florists, with comprehensive services to enhance franchise profitability. Lantern Petals works with some of the country's largest and most progressive supermarkets to provide franchisee ownership and operation of their strategically important floral departments.</p>
    <p>Supermarkets find that Lantern Petals is able to improve their financial outcomes, provide attentive customer service and satisfaction, and lift the quality of the entire store environment.</p>
  </div>
</section>

<section class="abs partner" role="img" aria-label="Dimmed flower market stalls full of bouquets">
  <div class="partner-logo"><span class="ring"></span>Frostvale Group</div>
  <p>Lantern Petals operates in partnership with Frostvale Group, the leading franchisor of sushi stations and pre-packaged fruit &amp; vegetable departments to supermarkets across the United States and United Kingdom.&nbsp; Lantern Petals' combination of floral and supermarket franchising expertise guarantees that consumers, franchisees and supermarket partners each receive exceptional service and value.</p>
</section>

<section class="abs gallery">
  <div class="tile t1" role="img" aria-label="Bouquet of red roses and white hydrangeas"></div>
  <div class="tile t2" role="img" aria-label="Florist selecting flowers from buckets"></div>
  <div class="tile t3" role="img" aria-label="Flower shop storefront with potted plants"></div>
  <div class="tile t4" role="img" aria-label="Happy florist in apron behind flower display"></div>
</section>

<section>
  <h2 class="abs script testi-head">What Our Customers <em>Say</em></h2>
  <div class="abs divider testi-div"><i></i><b></b><i></i></div>
  <div class="abs arrow prev"><svg width="10" height="10" viewBox="0 0 10 10"><path d="M6.5 1.5 3 5l3.5 3.5" stroke="#1f1f1f" stroke-width="2" fill="none"/></svg></div>
  <div class="abs arrow next"><svg width="10" height="10" viewBox="0 0 10 10"><path d="M3.5 1.5 7 5 3.5 8.5" stroke="#fff" stroke-width="2" fill="none"/></svg></div>
  <div class="abs card" style="left:142px">
    <div class="avatar" role="img" aria-label="Customer portrait"></div>
    <p>"Lorem ipsum dolor sit amet, consectetur adipiscing elit, sed do eiusmod tempor incididunt ut labore et dolore magna aliqua. Ut enim ad minim veniam, quis nostrud exercitation ullamco laboris nisi ut aliquip ex ea commodo consequat.</p>
    <div class="who script">Thomas <em>Hale</em></div>
    <div class="stars">★★★★★</div>
  </div>
  <div class="abs card" style="left:456px">
    <div class="avatar" role="img" aria-label="Customer portrait"></div>
    <p>"Lorem ipsum dolor sit amet, consectetur adipiscing elit, sed do eiusmod tempor incididunt ut labore et dolore magna aliqua. Ut enim ad minim veniam, quis nostrud exercitation ullamco laboris nisi ut aliquip ex ea commodo consequat.</p>
    <div class="who script">Lora <em>Whitfield</em></div>
    <div class="stars">★★★★★</div>
  </div>
  <div class="abs card" style="left:770px">
    <div class="avatar" role="img" aria-label="Customer portrait"></div>
    <p>"Lorem ipsum dolor sit amet, consectetur adipiscing elit, sed do eiusmod tempor incididunt ut labore et dolore magna aliqua. Ut enim ad minim veniam, quis nostrud exercitation ullamco laboris nisi ut aliquip ex ea commodo consequat.</p>
    <div class="who script">John <em>Marsh</em></div>
    <div class="stars">★★★★★</div>
  </div>
</section>

<footer class="abs footer">
  <h3 class="script fhead" style="left:142px">Quick Links</h3>
  <div class="fdiv" style="left:142px"><i></i><b></b><i></i></div>
  <div class="links">Home<br>About Us<br>For Supermarkets<br>For Franchisees<br>Contact Us</div>
  <h3 class="script fhead" style="left:412px">Contact Details</h3>
  <div class="fdiv" style="left:412px"><i></i><b></b><i></i></div>
  <ul class="fcontact">
    <li><span class="ic"><svg width="14" height="18" viewBox="0 0 14 18"><path d="M7 0a7 7 0 0 0-7 7c0 5 7 11 7 11s7-6 7-11a7 7 0 0 0-7-7z" fill="#fff"/><circle cx="7" cy="7" r="2.5" fill="#f0a500"/></svg></span><span>123, Building Name, Street<br>City, State XY 123456</span></li>
    <li><span class="ic"><svg width="16" height="16" viewBox="0 0 24 24"><path fill="#fff" d="M6.6 10.8a15 15 0 0 0 6.6 6.6l2.2-2.2a1 1 0 0 1 1-.25 11.4 11.4 0 0 0 3.6.57 1 1 0 0 1 1 1V20a1 1 0 0 1-1 1A17 17 0 0 1 3 4a1 1 0 0 1 1-1h3.5a1 1 0 0 1 1 1c0 1.25.2 2.45.57 3.57a1 1 0 0 1-.25 1z"/></svg></span>123-456-7890</li>
    <li><span class="ic"><svg width="16" height="12" viewBox="0 0 24 18"><rect width="24" height="18" rx="2" fill="#fff"/><path d="M2 2l10 8 10-8" stroke="#f0a500" stroke-width="2" fill="none"/></svg></span>info@lanternpetals.com</li>
  </ul>
  <div class="flogo"><span class="brand-dot"></span><span class="brand-name">Lantern Petals</span></div>
  <div class="social"><i></i><i></i><i></i><i></i></div>
  <div class="frule"></div>
  <div class="copy">©2024 Lantern Petals. All Rights Reserved.</div>
</footer>

</body>
</html>
```